Modern Business Card for Larkwell 2018

Our company assumes the best about people. We are creating an online community of entrepreneurs and business leaders who struggle with marketing their business online.

This business card should POP! We recently got a new logo and are launching a new website next month, so our business cards should make a statement that feels:
-Fresh
-Smart
-Trustworthy
-Fun

Target Market(s)

small business owners, entrepreneurs

Industry/Entity Type

Digital Marketing

Contact Information for Business Card

Dimensions: 3.5" x 2"

Font styles to use
Sans Serif

Colors
f37122
ffffff

Requirements
Must have
• We need a business card with a modern, bold design. We will use one side of the card as a lead-generation offer, so text on one side will need to fit up to 140 characters. The business card should stick to our core colors (orange, black, and white).
Nice to have
• We think a vertical "portrait" design could be interesting.
Should not have
• Should not look like a traditional business card. The round icon should stand out from a distance.

```html
<!DOCTYPE html>
<html lang="en">
<head>
<meta charset="utf-8">
<title>Larkwell Business Card</title>
<link href="https://fonts.googleapis.com/css2?family=Roboto:wght@400;500;700;900&family=Caveat:wght@600&display=swap" rel="stylesheet">
<style>
  :root {
    --orange: #f26828;
    --white: #ffffff;
    --paper: #f1f1f1;
    --ink: #222222;
    --grey: #4a4a4a;
    --stage: #e6e3df;
  }
  html, body {
    margin: 0;
    padding: 0;
    width: 1200px;
    height: 960px;
    overflow: hidden;
    background: var(--stage);
    font-family: "Roboto", sans-serif;
  }
  .canvas { position: relative; width: 1200px; height: 960px; }

  .card {
    position: absolute;
    border-radius: 22px;
    overflow: hidden;
    background: var(--paper);
  }

  /* Front */
  .card--front { left: 314px; top: 113px; width: 600px; height: 343px; }
  .front-band {
    position: absolute; left: 0; top: 0; bottom: 0; width: 82px;
    background: var(--orange);
  }
  .front-rule {
    position: absolute; left: 84px; top: 0; bottom: 0; width: 3px;
    background: #3a3330;
  }
  .brand-disc {
    position: absolute; left: 38px; top: 29px; width: 120px; height: 120px;
    border-radius: 50%;
    background: var(--orange);
    border: 3px solid var(--white);
    display: flex; align-items: center; justify-content: center;
  }
  .brand-disc__name {
    color: var(--white); font-weight: 700; font-size: 17px; letter-spacing: 1px;
  }
  .contact {
    position: absolute; right: 42px; top: 207px; text-align: right;
  }
  .contact__role { color: var(--ink); font-size: 15px; font-weight: 400; letter-spacing: .3px; }
  .contact__name {
    color: var(--orange); font-family: "Caveat", cursive; font-weight: 600;
    font-size: 42px; text-transform: uppercase;
    line-height: 1; margin-top: 14px;
  }
  .contact__email { color: var(--grey); font-size: 15px; font-weight: 500; margin-top: 10px; }

  /* Back */
  .card--back { left: 312px; top: 473px; width: 599px; height: 340px; }
  .offer {
    position: absolute; left: 0; top: 0; width: 100%; height: 217px;
    background: var(--orange); color: var(--white);
  }
  .brand-lockup {
    position: absolute; left: 0; top: 0; width: 316px; height: 217px;
  }
  .brand-lockup__dot {
    position: absolute; left: 141px; top: 58px; width: 34px; height: 34px;
    border-radius: 50%; background: var(--white);
  }
  .brand-lockup__name {
    position: absolute; left: 0; width: 316px; top: 108px; text-align: center;
    font-size: 38px; font-weight: 900; letter-spacing: 1.5px; line-height: 1;
  }
  .brand-lockup__tagline {
    position: absolute; left: 0; width: 316px; top: 151px; text-align: center;
    font-size: 11px; font-weight: 500; letter-spacing: 1px;
  }
  .offer__divider {
    position: absolute; left: 296px; top: 27px; width: 1px; height: 165px;
    background: rgba(255,255,255,.55);
  }
  .offer__copy { position: absolute; left: 322px; top: 29px; }
  .offer__headline {
    font-size: 18px; font-weight: 700; line-height: 21px; margin: 0; letter-spacing: .2px;
  }
  .offer__body { font-size: 15px; line-height: 20px; margin: 6px 0 0; }
  .offer__url { font-size: 19px; font-weight: 700; margin-top: 9px; }
  .notes__line {
    position: absolute; left: 35px; width: 520px; height: 1px; background: #333;
  }
  .notes__line--one { top: 259px; }
  .notes__line--two { top: 298px; }
</style>
</head>
<body>
<main class="canvas">
  <section class="card card--front">
    <div class="front-band"></div>
    <div class="front-rule"></div>
    <div class="brand-disc"><span class="brand-disc__name">LARKWELL</span></div>
    <div class="contact">
      <div class="contact__role">STORY MARKETING COACH</div>
      <div class="contact__name">Dana Whitcombe</div>
      <div class="contact__email">dana@larkwellnow.com</div>
    </div>
  </section>

  <section class="card card--back">
    <div class="offer">
      <div class="brand-lockup">
        <div class="brand-lockup__dot"></div>
        <div class="brand-lockup__name">LARKWELL</div>
        <div class="brand-lockup__tagline">SHARE IDEAS THAT SPARK MOMENTUM</div>
      </div>
      <div class="offer__divider"></div>
      <div class="offer__copy">
        <p class="offer__headline">REACH MORE PEOPLE.<br>MAKE MORE MONEY.<br>CREATE MORE IMPACT.</p>
        <p class="offer__body">Get your free Larkwell<br>Starter Package and our<br>marketing guide today at</p>
        <div class="offer__url">Larkwellnow.com/start</div>
      </div>
    </div>
    <div class="notes__line notes__line--one"></div>
    <div class="notes__line notes__line--two"></div>
  </section>
</main>
</body>
</html>
```